Coastline Premier Retreats Business Card Design

Design a business card for Coastline Premier Retreats. Look at the website for colors and reference. Card should have logo, name, title, office number, mobile number, email, URL and a tagline like, "Luxury Hotel & Resort Email Marketing" (This might change).

https://www.coastlinepremierretreats.example

The rest I will leave up to your imagination.

Contact Information for Business Card

Logo, name, title, office number, mobile number, email, URL and a tagline like, "Luxury Hotel & Resort Email Marketing" (This might change).

```html
<!DOCTYPE html>
<html lang="en">
<head>
<meta charset="utf-8">
<title>Coastline Premier Retreats – Business Card</title>
<link href="https://fonts.googleapis.com/css2?family=Open+Sans:wght@400;600;700&display=swap" rel="stylesheet">
<style>
  :root {
    --backdrop: #e4e4e2;
    --card-cream: #fdfcf3;
    --brand-orange: #ef7220;
    --ink: #151515;
    --divider: #2a2a2a;
    --sky: #b9cfe6;
    --sea: #5fa9ab;
    --foliage: #7f8f52;
  }
  * { box-sizing: border-box; margin: 0; padding: 0; }
  html, body {
    width: 1200px; height: 780px; overflow: hidden;
    background: var(--backdrop);
    font-family: "Open Sans", Arial, sans-serif;
  }
  .sheet {
    width: 1200px; height: 780px;
    display: flex; align-items: center; justify-content: center; gap: 40px;
  }
  .card {
    position: relative;
    width: 540px; height: 309px;
    overflow: hidden;
    box-shadow: 0 10px 28px rgba(0,0,0,.18);
  }

  /* Front */
  .card-front { background: var(--card-cream); }
  .front-photo {
    position: absolute; inset: 0;
    background:
      linear-gradient(180deg, var(--sky) 0%, #cfdde6 28%, transparent 42%),
      linear-gradient(100deg, var(--foliage) 0%, #8c9a62 30%, var(--sea) 52%, #78b4b0 70%, var(--foliage) 100%);
    opacity: .85;
  }
  .front-wordmark {
    position: absolute; left: 0; right: 0; top: 50%;
    transform: translateY(-50%);
    display: flex; align-items: center; justify-content: center; gap: 12px;
    font-weight: 700; font-size: 31px; letter-spacing: .5px;
    color: var(--ink);
  }
  .mark-square {
    width: 16px; height: 16px; background: var(--brand-orange); flex: none;
  }

  /* Back */
  .card-back { background: var(--card-cream); }
  .back-wordmark {
    position: absolute; left: 34px; top: 112px; width: 200px;
    display: flex; align-items: center; gap: 10px;
    font-weight: 700; font-size: 20px; line-height: 1.15;
    color: var(--ink);
  }
  .back-divider {
    position: absolute; left: 262px; top: 40px;
    width: 1px; height: 170px; background: var(--divider);
  }
  .contact-block {
    position: absolute; left: 290px; top: 42px; right: 20px;
  }
  .person-name {
    font-weight: 700; font-size: 25px; line-height: 1.1; color: var(--ink);
  }
  .person-name .given { color: var(--brand-orange); }
  .person-title {
    font-weight: 600; font-size: 13px; color: var(--ink); margin: 3px 0 14px;
  }
  .contact-list { list-style: none; }
  .contact-list li {
    display: flex; align-items: center; gap: 8px;
    font-size: 11.5px; line-height: 1.7; color: var(--ink);
    white-space: nowrap;
  }
  .contact-list svg { width: 12px; height: 12px; flex: none; }
  .tagline-band {
    position: absolute; left: 0; right: 0; bottom: 24px; height: 38px;
    background: var(--brand-orange);
    display: flex; align-items: center; justify-content: center;
    color: #fff; font-size: 14px; font-weight: 400; letter-spacing: .2px;
  }
</style>
</head>
<body>
<main class="sheet">

  <section class="card card-front" aria-label="Card front">
    <div class="front-photo" role="img" aria-label="Photograph of a rocky coastline with cypress trees above a turquoise cove"></div>
    <div class="front-wordmark">
      <span class="mark-square"></span>
      <span>Coastline Premier Retreats</span>
    </div>
  </section>

  <section class="card card-back" aria-label="Card back">
    <div class="back-wordmark">
      <span class="mark-square"></span>
      <span>Coastline Premier Retreats</span>
    </div>

    <div class="back-divider"></div>

    <div class="contact-block">
      <h1 class="person-name"><span class="given">Marta</span> Delacroix</h1>
      <p class="person-title">Co-Founder</p>
      <ul class="contact-list">
        <li>
          <svg viewBox="0 0 24 24" aria-hidden="true"><path fill="var(--brand-orange)" d="M6.6 10.8a15 15 0 0 0 6.6 6.6l2.2-2.2a1 1 0 0 1 1-.25 11.4 11.4 0 0 0 3.6.57 1 1 0 0 1 1 1V20a1 1 0 0 1-1 1A17 17 0 0 1 3 4a1 1 0 0 1 1-1h3.5a1 1 0 0 1 1 1c0 1.25.2 2.45.57 3.6a1 1 0 0 1-.25 1z"/></svg>
          (555) 014-2758
        </li>
        <li>
          <svg viewBox="0 0 24 24" aria-hidden="true"><rect x="6" y="2" width="12" height="20" rx="2" fill="none" stroke="var(--brand-orange)" stroke-width="2"/><circle cx="12" cy="18" r="1.2" fill="var(--brand-orange)"/></svg>
          (555) 019-7777
        </li>
        <li>
          <svg viewBox="0 0 24 24" aria-hidden="true"><circle cx="12" cy="12" r="9" fill="none" stroke="var(--brand-orange)" stroke-width="2"/><path d="M3 12h18M12 3c3 3 3 15 0 18M12 3c-3 3-3 15 0 18" fill="none" stroke="var(--brand-orange)" stroke-width="1.6"/></svg>
          www.coastlinepremierretreats.example
        </li>
        <li>
          <svg viewBox="0 0 24 24" aria-hidden="true"><rect x="2" y="5" width="20" height="14" rx="1.5" fill="var(--brand-orange)"/><path d="M3 6l9 7 9-7" fill="none" stroke="#fff" stroke-width="1.6"/></svg>
          info@coastlinepremierretreats.example
        </li>
      </ul>
    </div>

    <div class="tagline-band">Luxury Hotel &amp; Resort Email Marketing</div>
  </section>

</main>
</body>
</html>
```